Kindle Your Clients Book Cover

A book main title will be, "Kindle Your Clients"
The subtext will be, "Go to market with a story that sizzles"
Would like it to blend with my web site brand. You can find it here: www.kindleyourclients.example

Audience is business and revenue leaders for small, medium and large businesses. They have a new solution, or want to enter a new market, and they need to "inspire their buyers" meaning getting the buyers to want to change enough to overcome their status quo bias. They need a story that sizzles to do this.

```html
<!DOCTYPE html>
<html lang="en">
<head>
<meta charset="utf-8">
<title>Kindle Your Clients – Book Cover Wrap</title>
<link rel="stylesheet" href="https://fonts.googleapis.com/css2?family=Lexend:wght@400;500;600;700&display=swap">
<style>
  :root {
    --stage: #2b2b2b;
    --paper: #ffffff;
    --teal: #00a99d;
    --teal-deep: #0e6f67;
    --teal-mist: #bff0ea;
    --ink: #333333;
    --body-ink: #3a3a3a;
  }
  * { margin: 0; padding: 0; box-sizing: border-box; }
  html, body {
    width: 1200px; height: 1200px; overflow: hidden;
    background: var(--stage);
    font-family: "Lexend", sans-serif;
  }
  .cover-wrap {
    position: absolute; left: 40px; top: 206px;
    width: 1120px; height: 788px;
    background: var(--paper);
  }

  /* Back cover */
  .back-cover { position: absolute; left: 0; top: 0; width: 529px; height: 100%; }
  .back-heading {
    position: absolute; top: 50px; left: 0; width: 100%;
    text-align: center; font-size: 28px; font-weight: 600;
    letter-spacing: -1px; color: var(--ink);
  }
  .back-heading .accent { color: var(--teal); }
  .back-heading .slant { font-style: italic; }
  .blurb {
    position: absolute; left: 50px; top: 110px; width: 424px;
    font-size: 11.6px; line-height: 15.8px; color: var(--body-ink);
    text-align: justify; font-weight: 400;
  }
  .blurb p + p { margin-top: 15.8px; }

  /* Spine */
  .spine {
    position: absolute; left: 529px; top: 57px; width: 58px; height: 684px;
    display: flex; flex-direction: column; justify-content: space-between; align-items: center;
  }
  .spine-text {
    writing-mode: vertical-rl; font-size: 33px; font-weight: 600;
    letter-spacing: -1px; color: var(--ink); white-space: nowrap; line-height: 1;
  }
  .spine-text .accent { color: var(--teal); }
  .spine-text .slant { font-style: italic; }

  /* Front cover */
  .front-cover { position: absolute; left: 594px; top: 0; width: 526px; height: 100%; text-align: center; }
  .author-name {
    position: absolute; top: 46px; left: 0; width: 100%;
    font-size: 62px; font-weight: 600; letter-spacing: -2px; color: var(--ink);
  }
  .book-title {
    position: absolute; top: 148px; left: 0; width: 100%;
    font-weight: 700; font-size: 108px; line-height: 97px; letter-spacing: -4px; color: var(--ink);
  }
  .book-title span { display: block; }
  .book-title .accent { color: var(--teal); }
  .book-title .slant { font-style: italic; }
  .tagline {
    position: absolute; top: 500px; left: 0; width: 100%;
    font-size: 22px; font-weight: 500; color: var(--teal); letter-spacing: -0.3px;
  }
  .cover-photo {
    position: absolute; left: 0; bottom: 0; width: 100%; height: 250px;
    background: linear-gradient(180deg, var(--paper) 0%, var(--teal-mist) 35%, #5fcfc3 65%, var(--teal-deep) 100%);
  }
</style>
</head>
<body>
  <main class="cover-wrap">
    <section class="back-cover">
      <h2 class="back-heading"><span class="accent">KINDLE</span> YOUR <span class="slant">CLIENTS</span></h2>
      <div class="blurb">
        <p>Lorem ipsum dolor sit amet, consectetur adipiscing elit, sed do eiusmod tempor incididunt ut labore et dolore magna aliqua. Quis ipsum suspendisse ultrices gravida. Risus commodo viverra maecenas accumsan lacus vel facilisis. Lorem ipsum dolor sit amet, consectetur adipiscing elit, sed do eiusmod tempor incididunt ut labore et dolore magna aliqua. Quis ipsum suspendisse ultrices gravida. Risus commodo viverra maecenas accumsan lacus vel facilisis. Lorem ipsum dolor sit amet, consectetur adipiscing elit, sed do eiusmod tempor incididunt ut labore et dolore magna aliqua. Quis ipsum suspendisse ultrices gravida. Risus commodo viverra maecenas accumsan lacus vel facilisis.</p>
        <p>Lorem ipsum dolor sit amet, consectetur adipiscing elit, sed do eiusmod tempor incididunt ut labore et dolore magna aliqua. Quis ipsum suspendisse ultrices gravida. Risus commodo viverra maecenas accumsan lacus vel facilisis. Lorem ipsum dolor sit amet, consectetur adipiscing elit, sed do eiusmod tempor incididunt ut labore et dolore magna aliqua. Quis ipsum suspendisse ultrices gravida. Risus commodo viverra maecenas accumsan lacus vel facilisis. Lorem ipsum dolor sit amet, consectetur adipiscing elit, sed do eiusmod tempor incididunt ut labore et dolore magna aliqua. Quis ipsum suspendisse ultrices gravida. Risus commodo viverra maecenas accumsan lacus vel facilisis. Lorem ipsum dolor sit amet, consectetur adipiscing elit, sed do eiusmod tempor incididunt ut labore et dolore magna aliqua. Quis ipsum suspendisse ultrices gravida. Risus commodo viverra maecenas accumsan lacus vel facilisis.</p>
        <p>Lorem ipsum dolor sit amet, consectetur adipiscing elit, sed do eiusmod tempor incididunt ut labore et dolore magna aliqua. Quis ipsum suspendisse ultrices gravida. Risus commodo viverra maecenas accumsan lacus vel facilisis. Lorem ipsum dolor sit amet, consectetur adipiscing elit, sed do eiusmod tempor incididunt ut labore et dolore magna aliqua. Quis ipsum suspendisse ultrices gravida. Risus commodo viverra maecenas accumsan lacus vel facilisis. Lorem ipsum dolor sit amet, consectetur adipiscing elit, sed do eiusmod tempor incididunt ut labore et dolore magna aliqua. Quis ipsum suspendisse ultrices gravida. Risus commodo viverra maecenas accumsan lacus vel facilisis.</p>
      </div>
    </section>

    <section class="spine">
      <div class="spine-text"><span class="accent">KINDLE</span> YOUR <span class="slant">CLIENTS</span></div>
      <div class="spine-text">AUTHOR NAME</div>
    </section>

    <section class="front-cover">
      <div class="author-name">AUTHOR NAME</div>
      <h1 class="book-title">
        <span class="accent">KINDLE</span>
        <span>YOUR</span>
        <span class="slant">CLIENTS</span>
      </h1>
      <p class="tagline">Go to market with a story that sizzles</p>
      <div class="cover-photo" role="img" aria-label="Teal-toned photo of a cheering team in silhouette, arms raised, against a city skyline at sunrise"></div>
    </section>
  </main>
</body>
</html>
```